Boutique custom software development company needs new business card

Our nearly 20 year old custom software development company would like to better include the fact that we are now providing Bitcoin services. These new services are B2B include education (how to acquire and securely hold Bitcoin) and integrating Bitcoin payments into existing ecommerce sites or other existing systems. Please keep the card clean and simple. Attached is our current design and some other files. vextorial.com

Target Market(s)

businesses owners interested in long term relationship

Industry/Entity Type

Custom software development and Bitcoin

Contact Information for Business Card

Dale Parker, dale@vextorial.com, vextorial.com, (888) 555-VXTRL

Font styles to use
Other font styles liked:
• monospace

Requirements
Must have
• double-sided
Nice to have
• clean and simple
Should not have
• physical address

```html
<!DOCTYPE html>
<html lang="en">
<head>
<meta charset="UTF-8">
<title>Vextorial Business Card</title>
<link href="https://fonts.googleapis.com/css2?family=Montserrat:wght@400;500;600;800&display=swap" rel="stylesheet">
<style>
  :root {
    --bg: #d6d5d1;
    --card: #d8e1ed;
    --blue: #3b72ba;
    --orange: #f07f1e;
    --ink: #4b4f57;
  }
  * { margin: 0; padding: 0; box-sizing: border-box; }
  html, body { width: 1200px; height: 801px; overflow: hidden; }
  body {
    background: var(--bg);
    font-family: "Montserrat", Arial, sans-serif;
    position: relative;
  }
  .card {
    position: absolute;
    width: 540px;
    height: 309px;
    background: var(--card);
    border-bottom: 4px solid var(--orange);
    box-shadow: 0 10px 24px rgba(0,0,0,0.18);
  }
  .card-front { left: 36px; top: 120px; }
  .card-back { left: 624px; top: 372px; }

  .brand { display: flex; flex-direction: column; }
  .brand-name {
    font-weight: 800;
    color: var(--blue);
    letter-spacing: 1px;
    line-height: 1;
  }
  .brand-tagline {
    color: var(--blue);
    font-weight: 500;
    margin-top: 6px;
    white-space: nowrap;
  }
  .brand-services {
    color: var(--orange);
    font-weight: 600;
    margin-top: 6px;
    white-space: nowrap;
  }

  .card-front .brand { position: absolute; left: 44px; top: 50px; }
  .card-front .brand-name { font-size: 46px; }
  .card-front .brand-tagline { font-size: 17px; }
  .card-front .brand-services { font-size: 13px; }

  .person { position: absolute; left: 44px; top: 192px; }
  .person-name { font-weight: 800; font-size: 21px; letter-spacing: 1.5px; white-space: nowrap; }
  .person-first { color: var(--orange); }
  .person-last { color: var(--blue); }
  .person-role { font-size: 13px; color: var(--ink); margin-top: 4px; text-align: right; }

  .divider {
    position: absolute;
    left: 262px; top: 182px;
    width: 1px; height: 74px;
    background: var(--orange);
  }

  .contact { position: absolute; left: 282px; top: 184px; list-style: none; }
  .contact li {
    display: flex; align-items: center; gap: 8px;
    font-size: 13px; color: var(--ink);
    margin-bottom: 9px;
    white-space: nowrap;
  }
  .contact svg { width: 13px; height: 13px; fill: var(--blue); flex: none; }

  .card-back .brand { position: absolute; left: 0; right: 0; top: 92px; align-items: center; }
  .card-back .brand-name { font-size: 64px; }
  .card-back .brand-tagline { font-size: 22px; }
  .card-back .brand-services { font-size: 15px; margin-top: 10px; }
</style>
</head>
<body>
  <section class="card card-front" aria-label="Business card front">
    <div class="brand">
      <span class="brand-name">VEXTORIAL</span>
      <span class="brand-tagline">developer of custom applications</span>
      <span class="brand-services">+ Bitcoin services for business</span>
    </div>
    <div class="person">
      <div class="person-name"><span class="person-first">DALE</span> <span class="person-last">PARKER</span></div>
      <div class="person-role">Owner</div>
    </div>
    <div class="divider"></div>
    <ul class="contact">
      <li>
        <svg viewBox="0 0 24 24" aria-hidden="true"><path d="M6.6 10.8a15.1 15.1 0 0 0 6.6 6.6l2.2-2.2c.3-.3.7-.4 1-.2 1.1.4 2.3.6 3.6.6.6 0 1 .4 1 1V20c0 .6-.4 1-1 1A17 17 0 0 1 3 4c0-.6.4-1 1-1h3.5c.6 0 1 .4 1 1 0 1.3.2 2.5.6 3.6.1.3 0 .7-.2 1z"/></svg>
        (888) 555-VXTRL
      </li>
      <li>
        <svg viewBox="0 0 24 24" aria-hidden="true"><path d="M2 5h20v14H2z M2 5l10 8 10-8" /></svg>
        dale@vextorial.com
      </li>
      <li>
        <svg viewBox="0 0 24 24" aria-hidden="true"><circle cx="12" cy="12" r="10"/></svg>
        www.vextorial.com
      </li>
    </ul>
  </section>

  <section class="card card-back" aria-label="Business card back">
    <div class="brand">
      <span class="brand-name">VEXTORIAL</span>
      <span class="brand-tagline">developer of custom applications</span>
      <span class="brand-services">Bitcoin education &amp; payment integration</span>
    </div>
  </section>
</body>
</html>
```